Business software developers new website

We need to redesign our website. Our current website is http://www.plovencast.example/index.html, which is outdated and needs a new look. We moved out from web design and have concentrated more on the back end of the systems, for example, system support and security and cloud-based applications. Our major clients include both private and government sectors. We would like to see some designs that are all in one page, simple and clean. Prefer illustrator or obstructed images instead of real-life photos. Must look futuristic yet friendly. Attached the new logo for your references and good luck.

Target Market(s)

Medium to big company for their IT or data management. Either improve or upgrade their current system.

Industry/Entity Type

Business Software

Number of Pages Required

1 page

Colors

Designer to choose colors to be used in the design.

Requirements
Must have
• Simple and clean. Individual assets must be provided in the correct size and format(png or jpeg). Prefer Goggle fonts. Even though the logo color is red, grey and black, still prefer some modern colors that go well with red. When design, must consider the possibility to convert it into responsive.
Nice to have
• White background
Should not have
• real life photos, no slider

```html
<!DOCTYPE html>
<html lang="en">
<head>
<meta charset="utf-8">
<title>Plovencast</title>
<link href="https://fonts.googleapis.com/css2?family=Lato:wght@400;700;900&display=swap" rel="stylesheet">
<style>
:root{
  --red:#e4002b;
  --red-dark:#c8102e;
  --pink:#f5c0c6;
  --pink-soft:#f7d3d8;
  --shape:#e8e8ea;
  --text:#4d4d4d;
  --title:#3a3a3a;
  --white:#ffffff;
}
*{margin:0;padding:0;box-sizing:border-box}
html,body{width:1200px;height:3811px;overflow:hidden}
body{position:relative;background:var(--white);font-family:"Lato",sans-serif;color:var(--text)}
.abs{position:absolute}
.backdrop{position:absolute;left:0;top:0;width:1200px;height:3811px}
.logo{left:115px;top:48px;font-size:48px;font-weight:700;color:#2b2b2b;letter-spacing:1px;display:flex;align-items:center;gap:12px}
.logo-dot{width:14px;height:14px;background:var(--red);border-radius:50%}
.nav a{position:absolute;color:var(--white);font-weight:700;font-size:22px;text-decoration:none;white-space:nowrap}
.nav a.active::after{content:"";position:absolute;left:0;right:0;bottom:-14px;height:4px;background:var(--white)}
.hero-title{left:715px;top:186px;font-size:41px;font-weight:700;color:var(--white);white-space:nowrap}
.hero-text{left:727px;top:246px;width:447px;font-size:21px;line-height:32.6px;color:var(--white);text-align:justify}
.btn{display:flex;align-items:center;justify-content:center;font-weight:700;font-size:17px;color:var(--white);background:var(--red);width:129px;height:45px;text-decoration:none}
.btn-light{background:var(--white);color:var(--red);font-weight:400}
.section-title{font-size:41px;font-weight:700;color:var(--title);white-space:nowrap}
.copy{font-size:15.5px;line-height:25.8px;text-align:justify}
.service-icon{width:88px;height:88px}
.service-name{font-size:19px;font-weight:700;color:#222;white-space:nowrap}
.service-copy{font-size:15px;line-height:21px;text-align:justify}
.client-tile{top:2164px;width:245px;height:152px;background:#e6e6e6;display:flex;align-items:center;justify-content:center;font-size:26px;font-weight:700;color:#555}
.client-name{top:2326px;width:245px;text-align:center;font-size:19px;color:#333}
.philo-title{left:578px;top:2778px;font-size:38px;font-weight:700;color:var(--red)}
.rule{left:111px;width:978px;height:2px;background:var(--red)}
.news{left:127px;top:3358px;font-size:21px;font-weight:900;line-height:34px;color:#1e1e1e;text-transform:uppercase}
.news-form{left:740px;top:3371px;width:338px;height:48px;border:1px solid #d8d8d8;border-radius:24px;box-shadow:0 2px 6px rgba(0,0,0,.08)}
.news-form span{position:absolute;left:24px;top:14px;font-size:14px;color:#999}
.news-form b{position:absolute;right:3px;top:3px;width:96px;height:40px;border-radius:20px;background:var(--red);color:var(--white);font-size:14px;display:flex;align-items:center;justify-content:center}
.social{top:3531px;width:44px;height:44px;border-radius:50%;border:2px solid var(--red);background:var(--white);color:var(--red);font-size:11px;font-weight:700;display:flex;align-items:center;justify-content:center}
.footer-mark{left:118px;top:3590px;width:44px;height:44px;border-radius:50%;background:var(--red)}
.f-line{font-size:16.5px;color:var(--white);white-space:nowrap}
.f-icon{width:20px;height:20px}
.legal{left:623px;top:3789px;font-size:10px;color:var(--white);white-space:nowrap}
</style>
</head>
<body>

<svg class="backdrop" viewBox="0 0 1200 3811" aria-hidden="true">
  <defs>
    <linearGradient id="redGrad" x1="0" y1="0" x2="1" y2="1">
      <stop offset="0" stop-color="#e8193c"/>
      <stop offset="1" stop-color="#d9002a"/>
    </linearGradient>
  </defs>
  <path d="M488 0 L1200 0 L1200 466 L840 622 Q790 645 768 600 Z" fill="url(#redGrad)"/>
  <polygon points="-100,900 237,681 542,1036 89,1290 -200,1100" fill="var(--shape)" stroke="var(--shape)" stroke-width="60" stroke-linejoin="round"/>
  <polygon points="-200,1650 140,1399 501,1746 40,2020" fill="var(--shape)" stroke="var(--shape)" stroke-width="60" stroke-linejoin="round"/>
  <polygon points="1050,2065 727,2383 1160,2680 1400,2300" fill="var(--shape)" stroke="var(--shape)" stroke-width="60" stroke-linejoin="round"/>
  <polygon points="-20,2810 449,2746 545,3142 158,3215 -60,3100" fill="var(--shape)" stroke="var(--shape)" stroke-width="60" stroke-linejoin="round"/>
  <rect x="-40" y="622" width="151" height="64" rx="32" fill="var(--pink)"/>
  <polygon points="318,625 343,610 352,635 327,650" fill="var(--pink)"/>
  <polygon points="237,1307 262,1292 298,1313 275,1348 240,1330" fill="var(--pink)"/>
  <polygon points="937,1295 1003,1295 995,1357 930,1357" fill="var(--pink)"/>
  <rect x="1017" y="1310" width="230" height="53" rx="26" fill="var(--pink)"/>
  <rect x="799" y="1407" width="390" height="65" rx="32" fill="#f4c2cc"/>
  <polygon points="1110,2040 1145,1998 1200,2025 1165,2070" fill="var(--pink)"/>
  <polygon points="237,2655 275,2615 330,2645 295,2688" fill="var(--pink)"/>
  <path d="M860 2719 L915 2719 L940 2768 L860 2768 A24 24 0 0 1 860 2719 Z" fill="var(--pink-soft)"/>
  <polygon points="948,2719 1200,2719 1200,2768 975,2768" fill="var(--pink-soft)"/>
  <path d="M237 3197 L405 3197 L385 3241 L237 3241 A22 22 0 0 1 237 3197 Z" fill="#ee9aa6"/>
  <polygon points="412,3197 440,3197 420,3241 392,3241" fill="#ee9aa6"/>
  <path d="M448 3197 L468 3197 A22 22 0 0 1 468 3241 L428 3241 Z" fill="#ee9aa6"/>
  <path d="M163 3811 L255 3570 Q275 3520 330 3515 L520 3505 Q900 3520 1100 3660 Q1180 3720 1200 3770 L1200 3811 Z" fill="url(#redGrad)"/>
</svg>

<header>
  <div class="abs logo">plovencast<span class="logo-dot"></span></div>
  <nav class="nav">
    <a class="active" href="#" style="left:552px;top:56px">Home</a>
    <a href="#" style="left:661px;top:56px">Our Services</a>
    <a href="#" style="left:833px;top:56px">Our Clients</a>
    <a href="#" style="left:993px;top:56px">Contacts</a>
  </nav>
</header>

<section class="hero">
  <div class="abs" role="img" aria-label="Illustration of a woman working at a laptop on a desk beneath a floating system diagram" style="left:44px;top:163px;width:511px;height:370px;background:radial-gradient(ellipse at 50% 60%,#ececf2 0%,#f6f6f9 55%,#ffffff 80%)"></div>
  <h1 class="abs hero-title">Welcome To Plovencast</h1>
  <p class="abs hero-text">We build and look after the back-end systems that keep businesses running, with system support, security and cloud-based applications for private and government clients. We are known for reliable results and an individual approach to each customer.</p>
  <a class="abs btn btn-light" href="#" style="left:734px;top:434px">Read More</a>
</section>

<section class="about">
  <h2 class="abs section-title" style="left:127px;top:848px">About Us</h2>
  <p class="abs copy" style="left:129px;top:920px;width:341px">We support, secure and upgrade the systems behind medium and large organisations in the private and government sectors. We are known for reliable infrastructure, careful data management and our individual approach to each customer. Our company moves current systems to the cloud and keeps them safe, all at very competitive prices!</p>
  <a class="abs btn" href="#" style="left:129px;top:1125px">Read More</a>
  <div class="abs" role="img" aria-label="Illustration of an engineer seated before a wall of blue monitors" style="left:574px;top:790px;width:548px;height:290px;border-radius:45% 55% 50% 50% / 40% 40% 60% 60%;background:linear-gradient(135deg,#e6ecfb 0%,#cfdcfa 55%,#4a86f0 100%)"></div>
</section>

<section class="services">
  <h2 class="abs section-title" style="left:41px;top:1574px">Our Services</h2>
  <p class="abs copy" style="left:41px;top:1637px;width:338px">We take on projects from mid-sized companies to large government agencies. We are also extremely experienced in the long term support of comprehensive business systems, providing first class monitoring, maintenance, security, data management and upgrades.</p>
  <a class="abs btn" href="#" style="left:43px;top:1841px">Read More</a>

  <svg class="abs service-icon" style="left:577px;top:1508px" viewBox="0 0 88 88" fill="none" stroke="#8a1c2c" stroke-width="2.5">
    <rect x="2" y="2" width="84" height="60" rx="3"/><line x1="2" y1="52" x2="86" y2="52"/>
    <line x1="44" y1="62" x2="44" y2="76"/><line x1="26" y1="80" x2="62" y2="80"/>
    <polyline points="14,36 28,36 34,20 42,44 50,28 56,36 74,36"/>
  </svg>
  <h3 class="abs service-name" style="left:704px;top:1534px">System Support</h3>
  <p class="abs service-copy" style="left:704px;top:1563px;width:373px">Your systems need to run day and night. We monitor, maintain and upgrade them so your staff never wait on slow or failing tools.</p>

  <svg class="abs service-icon" style="left:693px;top:1658px" viewBox="0 0 88 88" fill="none" stroke="#c8102e" stroke-width="2.5">
    <rect x="2" y="12" width="84" height="60" rx="3"/><line x1="44" y1="72" x2="44" y2="80"/><line x1="24" y1="84" x2="64" y2="84"/>
    <path d="M28 52 A10 10 0 0 1 30 32 A14 14 0 0 1 56 30 A11 11 0 0 1 60 52 Z"/>
  </svg>
  <h3 class="abs service-name" style="left:829px;top:1673px">Cloud Applications</h3>
  <p class="abs service-copy" style="left:831px;top:1703px;width:256px">We build robust, scalable cloud apps and make sure they stay that way, from migration to daily running.</p>

  <svg class="abs service-icon" style="left:577px;top:1788px" viewBox="0 0 88 88" fill="none" stroke="#e0707e" stroke-width="2.5">
    <path d="M44 6 L74 16 L74 40 Q74 66 44 82 Q14 66 14 40 L14 16 Z"/>
    <rect x="32" y="38" width="24" height="20" rx="2" stroke="#8a1c2c"/>
    <path d="M36 38 L36 32 A8 8 0 0 1 52 32 L52 38" stroke="#8a1c2c"/>
  </svg>
  <h3 class="abs service-name" style="left:703px;top:1825px">Security</h3>
  <p class="abs service-copy" style="left:703px;top:1853px;width:385px">Beside using the latest techniques to protect your servers, data and users, we audit your current systems and set up ongoing threat monitoring.</p>
</section>

<section class="clients">
  <div class="abs client-tile" style="left:35px">Brightmill</div>
  <div class="abs client-tile" style="left:290px">Corvano</div>
  <div class="abs client-tile" style="left:530px;top:2161px">Tessella Bio</div>
  <div class="abs client-name" style="left:35px">Brightmill</div>
  <div class="abs client-name" style="left:282px;top:2328px">Corvano</div>
  <div class="abs client-name" style="left:524px">Tessella Bio</div>

  <h2 class="abs section-title" style="left:946px;top:2246px">Our Clients</h2>
  <p class="abs copy" style="left:802px;top:2309px;width:338px;text-align-last:right">We support organisations from mid-sized firms to government departments. We are also extremely experienced in the long term support of comprehensive business systems providing first class security, maintenance, cloud hosting and upgrades.</p>
  <a class="abs btn" href="#" style="left:1012px;top:2495px;width:130px">Read More</a>
</section>

<section class="philosophy">
  <div class="abs" role="img" aria-label="Illustration of two colleagues seated at a shared computer desk beside a potted plant" style="left:81px;top:2812px;width:407px;height:303px;border-radius:30px;background:linear-gradient(180deg,#e4e4ea 0%,#d9dbe6 60%,#c8d3f0 100%)"></div>
  <h2 class="abs philo-title">PHILOSOPHY</h2>
  <p class="abs copy" style="left:580px;top:2850px;width:486px;font-size:15px;line-height:30px">As systems specialists, we understand that a secure and reliable back end is a vital part of every modern organisation. This is why our support and cloud team work with all of our clients to keep their data safe and their systems ready for growth.</p>
  <a class="abs btn" href="#" style="left:583px;top:3013px">Read More</a>
</section>

<section class="newsletter">
  <div class="abs rule" style="top:3309px"></div>
  <p class="abs news">Build your own future<br>Join many task and get 100% boost</p>
  <div class="abs news-form"><span>Enter Email Address</span><b>SEND</b></div>
  <div class="abs rule" style="top:3509px"></div>
</section>

<footer>
  <div class="abs social" style="left:891px">Feed</div>
  <div class="abs social" style="left:959px">Post</div>
  <div class="abs social" style="left:1027px">Pics</div>
  <div class="abs footer-mark"></div>

  <svg class="abs f-icon" style="left:265px;top:3629px" viewBox="0 0 20 20" fill="#fff"><path d="M10 2 L19 10 L16 10 L16 18 L12 18 L12 13 L8 13 L8 18 L4 18 L4 10 L1 10 Z"/></svg>
  <div class="abs f-line" style="left:308px;top:3628px">info@plovencast.example</div>
  <svg class="abs f-icon" style="left:265px;top:3674px" viewBox="0 0 20 20" fill="#fff"><path d="M4 1 L8 5 L6 8 Q8 12 12 14 L15 12 L19 16 L16 19 Q7 19 1 4 Z"/></svg>
  <div class="abs f-line" style="left:308px;top:3674px">61 7 5550 0142</div>
  <svg class="abs f-icon" style="left:265px;top:3718px" viewBox="0 0 20 20" fill="#fff"><path d="M10 1 Q3 1 3 8 Q3 12 10 19 Q17 12 17 8 Q17 1 10 1 Z M10 5 A3 3 0 1 0 10 11 A3 3 0 1 0 10 5 Z" fill-rule="evenodd"/></svg>
  <div class="abs f-line" style="left:308px;top:3718px;line-height:25px">14 Harbour Lane<br>Elmsford, NY 1920</div>

  <div class="abs f-line" style="left:516px;top:3629px">Home</div>
  <div class="abs f-line" style="left:516px;top:3660px">Our Services</div>
  <div class="abs f-line" style="left:516px;top:3690px">Our Clients</div>
  <div class="abs f-line" style="left:516px;top:3720px">Contacts</div>

  <div class="abs f-line" style="left:663px;top:3628px">Terms&amp; Conditions</div>
  <div class="abs f-line" style="left:663px;top:3658px">Privacy Policy</div>
  <div class="abs f-line" style="left:663px;top:3688px">Support</div>
  <div class="abs f-line" style="left:663px;top:3718px">Newsletter</div>

  <div class="abs legal">© 2019 All Rights Reserved | Privacy Policy | Terms and Conditions</div>
</footer>

</body>
</html>
```